Bulldog themed background for Real Estate Purchase Letter

I need a phantom background or watermark on a standard 8 1/2" x 11" paper. I am going to put a letter over the background. I want a bulldog theme that is cute, funny and original. This letter is for a real estate project and we want to capture the person sub-consciously . Attached is my personal dogs. If you want to use them you can but not required. I have attached the letter that I am trying to emulate. I want bulldogs not horses.

Target Market(s)

45 years old and higher

Industry/Entity Type

Real Estate

Font styles to use
Serif
Sans Serif

Colors

Designer to choose colors to be used in the design.

Requirements
Must have
• fun, happiness, reassuring,
Should not have
• violence, negativity, unhappy

```html
<!DOCTYPE html>
<html lang="en">
<head>
<meta charset="utf-8">
<title>Homeowner Letter – Bulldog Background</title>
<link rel="stylesheet" href="https://fonts.googleapis.com/css2?family=Inter:wght@400&family=EB+Garamond:wght@400&family=Pinyon+Script&display=swap">
<style>
  :root {
    --paper: #ffffff;
    --coat: #e0d4c3;
    --coat-light: #ebe3d8;
    --chest: #f7f3ee;
    --blush: #f6dbe8;
    --ink: #1e1e1e;
  }
  * { margin: 0; padding: 0; box-sizing: border-box; }
  html, body { width: 848px; height: 1200px; overflow: hidden; background: var(--paper); }
  .letter {
    position: relative;
    width: 848px;
    height: 1200px;
    background: var(--paper);
    font-family: "Inter", Arial, sans-serif;
    color: var(--ink);
    overflow: hidden;
  }
  .mascot-area {
    position: absolute;
    left: 0; top: 0;
    width: 848px; height: 1200px;
  }
  .letter-content {
    position: absolute;
    left: 76px;
    top: 0;
    width: 700px;
    font-size: 15.5px;
    line-height: 20.8px;
    white-space: nowrap;
  }
  .letter-heading {
    position: absolute;
    top: 79px;
    text-transform: uppercase;
    font-size: 15.5px;
    line-height: 20.8px;
    font-weight: 400;
  }
  .salutation { position: absolute; top: 293px; }
  .letter-body { position: absolute; top: 355px; }
  .letter-body p { margin: 0; }
  .letter-body .gap { margin-top: 20.8px; }
  .closing {
    position: absolute;
    top: 954px;
    font-family: "EB Garamond", Georgia, serif;
    font-size: 16.5px;
  }
  .signature {
    position: absolute;
    top: 1000px;
    font-family: "Pinyon Script", cursive;
    font-size: 30px;
    line-height: 40px;
  }
  .postscript { position: absolute; top: 1066px; }
</style>
</head>
<body>
<main class="letter">
  <svg class="mascot-area" role="img" aria-label="Soft full-page watermark illustration of a cute, happy bulldog puppy in beige and white, standing with its tongue out behind the letter" viewBox="0 0 848 1200" xmlns="http://www.w3.org/2000/svg">
    <defs>
      <radialGradient id="coatTone" cx="50%" cy="62%" r="62%">
        <stop offset="0%" stop-color="#f7f3ee"/>
        <stop offset="35%" stop-color="#ebe3d8"/>
        <stop offset="75%" stop-color="#e0d4c3"/>
        <stop offset="100%" stop-color="#e0d4c3" stop-opacity="0.85"/>
      </radialGradient>
    </defs>
    <rect x="100" y="30" width="700" height="1150" rx="160" fill="url(#coatTone)"/>
  </svg>

  <div class="letter-content">
    <h1 class="letter-heading">Nequiant iantiis mos-<br>sum, aliqui ament.<br>Uptatur modi volor-<br>io dem</h1>

    <p class="salutation">Dear Homeowner,</p>

    <div class="letter-body">
      <p>Erchicat emolore rumquiam, ommolori doluptatem. Equae repre minusdam, simi, uta<br>solupturiam ilitati omnis exerum que modis recte dolorum et quatend ebitati adit, quideli-<br>bus ene prent.Pos dendae nus. Boreni to ipsum cusaperchil eum reneces dolor ant faccae<br>eatiaeped earias aut perepel luptatium sum senditae omni blaccus exerumque earum<br>sametur?</p>
      <p>Aquam, omnia ni si quibus am incius velest, tor aut apidige nimusae plabore stibus as<br>est, cone eumque eost, exerchit ullecum natur accus ea dolupta ssunditam, occulparum<br>natque sit aut eos iminvel isitaquias alicias mo qui offici ut et aut asimporem cuptat reptas<br>estius es magniaes natem faccuptaquos dolupta tempos mos reped quas dolupta sum et<br>quas doloratem ne voloressus nat que est maxime voluptat eum facearum sus raestis ul-<br>parum nectem dis dolent, ut velectem dolupta turepta erchit, occulpa doleste quat volorera<br>ipsae. Nem resci sectiberiant am laudit, nonsequi consequos accusamus.</p>
      <p class="gap">Hillupt atiuritios aut exerchi ciditam cores simusant, sectat.</p>
      <p>Ped exeraturem is am qui qui ommoluptatet aspidi ut idustiorest, cus ut explab int volup-<br>taerit illaudit vollistibus dem diamet ut atium faceatios eum num solupid ulluptiossi bea-<br>quat umquia voluptint.</p>
      <p class="gap">Evel magnate omnisin conet restibusda velland enderruntis abor alisquate lit quiam quo<br>quam dolupta volorpo reiunt et arum iminti sit ommosam dolupit, volecto con resti nus,<br>que ne porepudam, niam, quaturit, sinulla boresequam harit estrum untiamenim eatatur<br>sum volendis volor si aditint id et volore consed enia sam aut eicae voluptus endit utate<br>quo volorrum doluptus, nitiuscia quunt laboribus qui comniame vitasse odisquas anihicil<br>ident.</p>
      <p>Equam ande cuptat et res estrumquas dolorunt, utatae latiscit enda comni imusdande pra<br>conem que res et aut essedig nienect otatessin pore solorem fugiamus, teceatibus quianiet<br>omnienis dolum erum et repelig endaestrum que antiae sit labore, et voluptis</p>
    </div>

    <p class="closing">Yours Sincerely,</p>
    <p class="signature">SIGNATURE</p>
    <p class="postscript">PS. If you would like to email us information and pictures<br>of your property please send them to ;</p>
  </div>
</main>
</body>
</html>
```